Bulldog themed background for Real Estate Purchase Letter

I need a phantom background or watermark on a standard 8 1/2" x 11" paper. I am going to put a letter over the background. I want a bulldog theme that is cute, funny and original. This letter is for a real estate project and we want to capture the person sub-consciously . Attached is my personal dogs. If you want to use them you can but not required. I have attached the letter that I am trying to emulate. I want bulldogs not horses.

Target Market(s)

45 years old and higher

Industry/Entity Type

Real Estate

Font styles to use
Serif
Sans Serif

Colors

Designer to choose colors to be used in the design.

Requirements
Must have
• fun, happiness, reassuring,
Should not have
• violence, negativity, unhappy

```html
<!DOCTYPE html>
<html lang="en">
<head>
<meta charset="UTF-8">
<title>Real Estate Purchase Letter</title>
<link href="https://fonts.googleapis.com/css2?family=Open+Sans:wght@300;400;600&family=Montserrat:wght@500&display=swap" rel="stylesheet">
<style>
  :root {
    --brand-blue: #0a5cc4;
    --brand-blue-deep: #0747b0;
    --brand-cyan: #19b2ee;
    --paper: #ffffff;
    --ink: #3a3a3a;
    --ink-strong: #2b2b2b;
    --watermark-light: #f3f1ee;
    --watermark-mid: #dedad5;
  }
  * { margin: 0; padding: 0; box-sizing: border-box; }
  html, body { width: 850px; height: 1200px; overflow: hidden; background: var(--paper); }
  .letter-page {
    position: relative;
    width: 850px;
    height: 1200px;
    background: var(--paper);
    overflow: hidden;
    font-family: "Open Sans", Arial, sans-serif;
    color: var(--ink);
  }
  .bulldog-watermark {
    position: absolute;
    left: 30px;
    top: 160px;
    width: 790px;
    height: 930px;
    border-radius: 46% 44% 40% 42% / 30% 32% 36% 38%;
    background: radial-gradient(ellipse at 50% 55%, var(--watermark-mid) 0%, var(--watermark-light) 55%, rgba(255,255,255,0) 78%);
    opacity: 0.9;
  }
  .wave { position: absolute; left: 0; top: 0; width: 850px; height: 1200px; }
  .agent-id {
    position: absolute;
    left: 67px;
    top: 48px;
    font-family: "Montserrat", "Open Sans", sans-serif;
    font-weight: 500;
    font-size: 17.5px;
    line-height: 25px;
    color: var(--paper);
  }
  .letter-body {
    position: absolute;
    left: 69px;
    top: 198px;
    width: 712px;
    font-size: 17.3px;
    font-weight: 300;
    line-height: 30.5px;
  }
  .letter-body strong { font-weight: 600; color: var(--ink-strong); }
  .recipient { margin-bottom: 30px; }
  .salutation { margin-bottom: 30px; }
  .paragraph { text-indent: 40px; text-align: justify; margin-bottom: 30px; }
  .closing { margin-top: 0; margin-bottom: 33px; }
  .signature { font-weight: 600; color: var(--ink-strong); }
</style>
</head>
<body>
<main class="letter-page">
  <div class="bulldog-watermark" role="img" aria-label="Faint watermark photo of a smiling white bulldog with its tongue out"></div>

  <svg class="wave" viewBox="0 0 850 1200" aria-hidden="true">
    <defs>
      <linearGradient id="topBand" x1="0" y1="0" x2="1" y2="1">
        <stop offset="0" stop-color="var(--brand-blue-deep)"/>
        <stop offset="1" stop-color="var(--brand-blue)"/>
      </linearGradient>
      <linearGradient id="bottomBand" x1="0" y1="0" x2="1" y2="1">
        <stop offset="0" stop-color="var(--brand-blue)"/>
        <stop offset="1" stop-color="var(--brand-blue-deep)"/>
      </linearGradient>
    </defs>
    <path fill="var(--brand-cyan)" d="M0 0 H560 C480 34 430 66 400 82 C335 110 255 120 165 132 C80 144 28 188 0 245 Z"/>
    <path fill="url(#topBand)" d="M0 0 H545 C470 28 420 58 388 72 C325 98 245 108 155 120 C75 132 25 172 0 228 Z"/>
    <path fill="var(--brand-cyan)" d="M190 1200 C285 1140 370 1098 462 1066 C555 1036 645 1036 715 1024 C790 1012 830 982 850 945 V1200 Z"/>
    <path fill="url(#bottomBand)" d="M207 1200 C300 1152 382 1114 472 1084 C562 1055 652 1054 722 1042 C792 1030 832 1002 850 968 V1200 Z"/>
  </svg>

  <p class="agent-id">Real Estate Agent ID :<br>#0192837465</p>

  <section class="letter-body">
    <p class="recipient"><strong>Mr. Outta Stateowner</strong><br>4821 Harbor Lane<br>Pinewood FL 34400-5360</p>
    <p class="salutation">Dear <strong>First Name</strong></p>
    <p class="paragraph">I am writing you, because I am interested in purchasing your property located at <strong>4821 Harbor Lane Pinewood FL 34400-5360</strong> I live nearby in Maplecrest and I puschages properties throught the state of PA Currently I am working on projects in the neighbourhood, which is how I learned of your property.</p>
    <p class="paragraph">Please call me at <strong>(XXX) XXXX-Local#</strong> so I can tell you how we can buy your property quickly, with no hassels and most importantly, at a fair price. I purchase the hous directly from you so there are no real estate commissions or extra fees coming out of your pocket. Furthermore, I always make cash offers so you never have to worry about delays resulting from a buyer trying to qualify for a mortgage and wasting your valuable time.</p>
    <p class="paragraph">I'will be glade to personally tell you more about how we can work together. All call are completely confidential and there is no obligation whatsoever. Even if you are not intersted in selling at thing time call <strong>(xxx) xxxx-xxxx</strong>, so I can help you with determining the value of your property. You should also keep this letter for your future reference, since things in life have a tendency to change unexpectedly. Thanks you for your time and consideration and I look forward to speaking with you.</p>
    <p class="closing">Sincerely,</p>
    <p class="signature">Dana Whitfield</p>
  </section>
</main>
</body>
</html>
```